Bry7Legal Letterhead

Need a new letterhead for my law firm.
IDENTIFYING INFORMATION BELOW:
Anselmo R Quintara III
Attorney at Law
Address: 2847 Larkspur Blvd, Ste 300, Dallas, TX 75204
Phone: 877-482-6017
Fax: 469-738-1452
Email: bry@bry7legal.example
Website: www.bry7legal.example

Colors
0054AA
0677BA
7BADD7
CADEEF
E8F1F8

Requirements
Must have
• Logo needs to be on the letterhead, along with identifying information which is included in the project description.

```html
<!DOCTYPE html>
<html lang="en">
<head>
<meta charset="utf-8">
<title>Bry7Legal Letterhead</title>
<link rel="stylesheet" href="https://fonts.googleapis.com/css2?family=Montserrat:wght@400;500&display=swap">
<style>
  :root {
    --backdrop: #e9eaec;
    --paper: #ffffff;
    --ink: #1d1d1f;
    --ink-soft: #3a3a3c;
    --accent: #1b9ad6;
    --band: #151515;
  }
  * { box-sizing: border-box; margin: 0; padding: 0; }
  html, body {
    width: 1200px; height: 874px; overflow: hidden;
    background: var(--backdrop);
    font-family: "Montserrat", Arial, sans-serif;
    color: var(--ink);
  }
  .letterhead {
    position: absolute; left: 317px; top: 37px;
    width: 566px; height: 800px;
    background: var(--paper);
    box-shadow: 0 6px 22px rgba(0,0,0,.12);
    overflow: hidden;
  }
  .bottom-band { position: absolute; inset: 0; width: 100%; height: 100%; }
  .bottom-band .band { fill: var(--band); }
  .bottom-band .stripe { fill: var(--accent); }

  .brand { position: absolute; left: 52px; top: 66px; }
  .brand-name {
    font-weight: 500; font-size: 24px; line-height: 1;
    color: var(--ink);
  }

  .contact {
    position: absolute; right: 48px; top: 54px; width: 170px;
    font-style: normal;
    font-size: 7.5px; line-height: 1.55; color: var(--ink-soft);
  }
  .contact ul { list-style: none; }
  .contact li { display: flex; align-items: center; gap: 5px; }
  .contact svg { width: 8px; height: 8px; fill: var(--accent); flex: none; }

  .letter-body {
    position: absolute; left: 52px; top: 150px; width: 450px;
    font-size: 8.6px; line-height: 1.6; color: var(--ink);
  }
  .recipient { margin-bottom: 2px; }
  .letter-body p { margin-bottom: 13px; }
  .closing { margin-top: 2px; }
  .signature {
    margin-top: 10px; width: 110px; height: 44px;
    background: linear-gradient(90deg, #f1f1f1, #e4e4e4);
  }
</style>
</head>
<body>
  <main class="letterhead">
    <svg class="bottom-band" viewBox="0 0 566 800" preserveAspectRatio="none" aria-hidden="true">
      <path class="band" d="M0 800 Q400 792 566 752 L566 800 Z"/>
      <path class="stripe" d="M300 790 Q460 774 566 738 L566 746 Q462 780 300 790 Z"/>
    </svg>

    <header class="brand">
      <div class="brand-name">Bry7Legal</div>
    </header>

    <address class="contact">
      <div>2847 Larkspur Blvd,</div>
      <div>Ste 300, Dallas, TX 75204</div>
      <ul>
        <li><svg viewBox="0 0 10 10"><path d="M2 0.5 L4 2.6 3 3.8 Q4.2 5.9 6.2 7 L7.4 6 9.5 8 8.2 9.5 Q3.6 9.2 0.5 1.8 Z"/></svg>877-482-6017</li>
        <li><svg viewBox="0 0 10 10"><rect x="2" y="0.5" width="6" height="3"/><rect x="0.5" y="4" width="9" height="4.5" rx="1"/></svg>469-738-1452</li>
        <li><svg viewBox="0 0 10 10"><path d="M0.5 2 L5 5.5 9.5 2 9.5 8.5 0.5 8.5 Z"/></svg>bry@bry7legal.example</li>
        <li><svg viewBox="0 0 10 10"><circle cx="5" cy="5" r="4.5"/></svg>www.bry7legal.example</li>
      </ul>
    </address>

    <section class="letter-body">
      <div class="recipient">Mr/s<br>First Name and Last Name<br>Company Name<br>Address</div>
      <p>Lorem Ipsum is simply dummy text of the printing and typesetting industry. Lorem Ipsum has been the industry's standard dummy text ever since the 1500s, when an unknown printer took a galley of type and scrambled it to make a type specimen book. It has survived not only five centuries, but also the leap into electronic typesetting, remaining essentially unchanged. It was popularised in the 1960s.</p>
      <p>The standard chunk of Lorem Ipsum used since the 1500s is reproduced below for those interested. Sections 1.10.32 and 1.10.33 from "de Finibus Bonorum et Malorum" by Cicero are also reproduced in their exact original form, accompanied by English versions from the 1914 translation by H. Rackham. Lorem ipsum dolor sit amet, consectetur adipiscing elit, sed do eiusmod tempor incididunt ut labore et dolore magna aliqua.</p>
      <p>It is a long established fact that a reader will be distracted by the readable content of a page when looking at its layout. The point of using Lorem Ipsum is that it has a more-or-less normal distribution of letters, as opposed to using 'Content here, content here', making it look like readable English. Many desktop publishing packages and web page editors now.</p>
      <div class="closing">Your Sincerely,</div>
      <div class="signature" role="img" aria-label="Handwritten signature"></div>
    </section>
  </main>
</body>
</html>
```